Web and Logo Design for eCommerce site

We're launching a sister brand and require a full design for the site.

The site must have an established feel and appeal to corporate and institutional buyers.
Updates

Just a note about the wireframe design:

The Search & Rescue / Coast Guard / NVDK, etc. in the header area aren't buttons or menu items, but rather just info (along the lines of a tagline).  Sort of a "who we serve" sort of thing.

Worth noting is that it's specifically geared towards LARGE BUYERS.  For example, a police force buying 200 headlamps and 85 pairs of gloves.  So they'll register + sign in and then add a bunch of items to a RFQ.

Aim for a professional, masculine design.

Target Market(s)

We will be selling outdoor gear to the military, law enforcement, fire and rescue and first responders.

Requirements
Must have
• We require:
- Logo (vector based)

Site:
- template page
* main site template, re-skinned version of our current site
* horizontal drop-down menu
- product listings page
* thumbnail view of products
- product details page
* including elements such as product image, color/size selector, descriptions and specs (again, based loosely on our current website)
- account management page
* illustrating basic data entry styles for text box, buttons, grid, etc.

The site needs to be given a responsive design, so 2 versions of each design should be presented for desktop + mobile views.

Additional funds are available if the designer is able to fully implement the designs into a responsive framework such as bootstrap.

Nice to have
• Clean, professional design similar to:

http://military.trailvexagear.com/gov/accessories/gloves.html

http://leaf.ombrivo.com/ProductFind.aspx?language=EN&category=Hardshell&subcat=Waterproof_Jackets

```html
<!DOCTYPE html>
<html lang="en">
<head>
<meta charset="utf-8">
<title>Army Parka with Liner Olive – NorthKit</title>
<link href="https://fonts.googleapis.com/css2?family=Open+Sans:wght@400;600;700&display=swap" rel="stylesheet">
<style>
:root{
  --bar:#1f2731;
  --nav:#252d36;
  --olive:#9aab45;
  --olive-dark:#5d6b2c;
  --tab:#5f6e32;
  --red:#c4161c;
  --page:#dfe7e7;
  --white:#ffffff;
  --text:#333a40;
  --muted:#555;
  --foot:#16110d;
  --foot-text:#c9c6c0;
  --field:#e6e6e6;
  --line:#dcdcdc;
}
*{box-sizing:border-box;margin:0;padding:0}
html,body{width:1013px;height:1200px;overflow:hidden}
body{font-family:"Open Sans",Arial,sans-serif;background:var(--page);color:var(--text);position:relative}
.abs{position:absolute}
a{color:inherit}

.top-bar{left:0;top:0;width:1013px;height:29px;background:var(--bar)}
.served{left:93px;top:0;line-height:29px;font-size:9px;color:#e8e8e8;white-space:nowrap}
.served span{margin:0 7px}
.social-dots{right:93px;top:5px;display:flex;gap:5px}
.social-dots i{width:18px;height:18px;border-radius:50%;background:#fff;display:block}

.header{left:0;top:29px;width:1013px;height:70px;background:var(--white)}
.brand{left:95px;top:44px;display:flex;align-items:center;gap:8px}
.brand-mark{width:36px;height:36px;background:var(--olive-dark);border-radius:50%}
.brand-name{font-size:30px;font-weight:700;color:#3d4420;line-height:1}
.contact{right:95px;top:56px;font-size:11px;color:#666;display:flex;align-items:center;gap:6px}

.main-nav{left:93px;top:100px;width:827px;height:35px;background:var(--nav);display:flex;align-items:center;padding-left:18px}
.main-nav a{text-decoration:none;font-size:12px;color:var(--olive);margin-right:24.5px}
.main-nav a.current{color:#fff;font-weight:600}
.search-btn{right:8px;top:7px;width:21px;height:21px;background:var(--olive)}

.panel{left:93px;top:143px;width:827px;height:747px;background:var(--white)}
.crumbs{left:108px;top:160px;font-size:11px}
.crumbs a{color:#222}
.crumbs span{margin:0 5px}

.photo-frame{left:107px;top:196px;width:368px;height:355px;border:1px solid #e3e3e3;background:#fff}
.photo{left:15px;top:8px;width:338px;height:338px;background:radial-gradient(ellipse at 50% 50%,#a98258 0%,#98714a 55%,#fff 72%)}
.thumb{top:565px;width:55px;height:54px;border:1px solid #ddd;background:radial-gradient(circle,#a47d53 0%,#9a744c 55%,#fff 75%)}
.arrow{top:586px;width:0;height:0;border-top:6px solid transparent;border-bottom:6px solid transparent}

.title{left:506px;top:189px;font-size:24px;font-weight:600;color:#1b1f22}
.desc{left:506px;top:228px;width:380px;font-size:10.5px;line-height:17px;color:var(--muted)}
.more{left:506px;top:304px;font-size:10px;color:var(--olive-dark)}

.price-label{top:336px;font-size:13.5px}
.price{top:350px;font-size:25px;font-weight:600}
.retail{left:506px;color:var(--olive-dark)}
.yours{left:619px;color:var(--red)}
.price-sep{top:337px;width:1px;height:46px;background:var(--line)}
.stock{left:773px;top:337px;font-size:10px;line-height:17px;color:#222}

.sizes{left:506px;top:403px;width:367px;border-collapse:collapse;font-size:11px;border:1px solid #ccc}
.sizes th{background:var(--nav);color:#fff;height:27px;font-weight:600;width:56px}
.sizes th:first-child{width:auto}
.sizes td{height:25px;border-top:1px solid #e5e5e5;text-align:center}
.sizes td:first-child{text-align:left;padding-left:15px;color:#222}
.sizes td+td{border-left:1px solid #e5e5e5}
.box{display:inline-block;width:10px;height:10px;border:1px solid #999;background:#f4f4f4}

.qty{left:506px;top:558px;width:85px;height:35px;border:1px solid #ccc;font-size:11px;padding:0 8px;display:flex;align-items:center;justify-content:space-between}
.qty i{width:13px;height:13px;border:1px solid #777;display:block;position:relative}
.qty i:after{content:"";position:absolute;left:2px;top:4px;border-left:4px solid transparent;border-right:4px solid transparent;border-top:4px solid #333}
.rfq{left:608px;top:558px;width:117px;height:35px;background:var(--red);color:#fff;font-size:15px;font-weight:700;display:flex;align-items:center;justify-content:center;border-radius:2px}
.rule{left:506px;top:609px;width:367px;height:1px;background:#e6e6e6}
.shares{left:509px;top:632px;display:flex;gap:10px;font-size:9px}
.share{display:flex;align-items:center;gap:3px}
.share b{height:16px;padding:0 5px;border:1px solid #bbb;border-radius:2px;line-height:14px;background:#f3f3f3;font-weight:600;color:#333}
.share.fb b{background:#3b5a9a;color:#fff;border-color:#3b5a9a}
.share em{font-style:normal;height:16px;border:1px solid #ccc;padding:0 4px;line-height:14px;color:#555}

.tab{top:694px;height:32px;font-size:14px;display:flex;align-items:center;justify-content:center;color:#fff;background:var(--tab)}
.tab.active{background:#f6f6f6;color:#222;border:1px solid #ddd;border-bottom:none;height:33px;z-index:2}
.tab-body{left:107px;top:726px;width:795px;height:143px;background:#f6f6f6;border:1px solid #ddd}
.overview{left:126px;top:748px;width:766px;font-size:10.6px;line-height:15px;color:#555}
.email{left:126px;top:836px;font-size:11px;color:var(--red);display:flex;align-items:center;gap:6px}

.footer{left:0;top:911px;width:1013px;height:289px;background:var(--foot)}
.f-head{top:942px;font-size:14px;font-weight:600;color:#fff}
.f-links{top:980px;list-style:none;font-size:11px;line-height:18.6px;color:var(--foot-text)}
.f-note{left:422px;top:981px;width:230px;font-size:10.5px;line-height:16px;color:var(--foot-text)}
.f-input{left:422px;top:1028px;width:214px;height:32px;background:#fff;display:flex}
.f-input span{flex:1;font-size:11px;color:#999;line-height:32px;padding-left:9px}
.f-input b{width:52px;background:#d0d0d0;font-weight:400;font-size:13px;color:#333;line-height:32px;text-align:center}
.field{left:735px;width:187px;background:var(--field);font-size:10px;color:#333;padding:5px 10px}
.submit{left:735px;top:1123px;width:72px;height:20px;background:var(--olive-dark);color:#e9efc8;font-size:10px;text-align:center;line-height:20px}
.copy{left:0;top:1159px;width:1013px;text-align:center;font-size:11px;color:#fff}
</style>
</head>
<body>

<div class="abs top-bar"></div>
<div class="abs served">SEARCH &amp;RECUE<span>|</span>COAST GUARD<span>|</span>NVDK<span>|</span>FIRE<span>|</span>MILIATRY<span>|</span>LAW ENFORCEMENT</div>
<div class="abs social-dots"><i></i><i></i><i></i><i></i></div>

<div class="abs header"></div>
<div class="abs brand"><div class="brand-mark"></div><div class="brand-name">NorthKit</div></div>
<div class="abs contact">
  <svg width="14" height="14" viewBox="0 0 24 24"><path d="M6.6 10.8a15 15 0 006.6 6.6l2.2-2.2c.3-.3.7-.4 1-.2 1.1.4 2.3.6 3.6.6.6 0 1 .4 1 1V20c0 .6-.4 1-1 1A17 17 0 013 4c0-.6.4-1 1-1h3.5c.6 0 1 .4 1 1 0 1.3.2 2.5.6 3.6.1.3 0 .7-.2 1z" fill="#999"/></svg>
  Call (+) 0800.555.019
  <svg width="16" height="14" viewBox="0 0 24 20" style="margin-left:8px"><path d="M2 7h20l-3 11H5z M7 7l5-6 5 6" fill="none" stroke="#777" stroke-width="2"/></svg>
  (0 item) - $0.00 &nbsp;▾
</div>

<nav class="abs main-nav">
  <a class="current" href="#">RESCUE GEAR</a>
  <a href="#">FOOTWEAR</a>
  <a href="#">CLOTHING</a>
  <a href="#">TENTS MATS SLEEPING BAGS</a>
  <a href="#">CAMPING GEAR</a>
  <a href="#">SNOW SPORTS</a>
  <a href="#">BRAND'S</a>
  <div class="abs search-btn">
    <svg width="21" height="21" viewBox="0 0 21 21"><circle cx="9" cy="9" r="4.5" fill="none" stroke="#fff" stroke-width="1.8"/><path d="M12.3 12.3l4 4" stroke="#fff" stroke-width="2"/></svg>
  </div>
</nav>

<div class="abs panel"></div>
<div class="abs crumbs"><a href="#">Rescue Gear</a><span>&gt;</span><a href="#">Helmet</a><span>&gt;</span><a href="#">Maze Helmet </a></div>

<div class="abs photo-frame"><div class="abs photo" role="img" aria-label="Tan army shirt laid flat, front view"></div></div>
<div class="abs arrow" style="left:165px;border-right:8px solid #3e4a20"></div>
<div class="thumb abs" style="left:193px" role="img" aria-label="Shirt thumbnail"></div>
<div class="thumb abs" style="left:255px" role="img" aria-label="Shirt thumbnail"></div>
<div class="thumb abs" style="left:316px" role="img" aria-label="Shirt thumbnail"></div>
<div class="abs arrow" style="left:391px;border-left:8px solid #3e4a20"></div>

<h1 class="abs title">Army Parka with Liner Olive</h1>
<p class="abs desc">All the actual measurements given on the site as "armpit to armpit x 2" refer to the measurements of the garment and not the size it will fit.<br>The best way of checking if an item will fit is to measure a similar garment you have which fits well and compare the measurements.</p>
<div class="abs more">+ <a href="#">more</a></div>

<div class="abs price-label retail">RETAIL PRICE</div>
<div class="abs price retail">$199.99</div>
<div class="abs price-sep" style="left:603px"></div>
<div class="abs price-label yours">YOUR PRICE LEVEL</div>
<div class="abs price yours">$150.99</div>
<div class="abs price-sep" style="left:755px"></div>
<div class="abs stock">Free Canada Shipping<br>In Stock<br>Ship in 24 hours</div>

<table class="abs sizes">
  <tr><th></th><th>S</th><th>M</th><th>L</th><th>XL</th></tr>
  <tr><td>Orange</td><td><i class="box"></i></td><td><i class="box"></i></td><td><i class="box"></i></td><td><i class="box"></i></td></tr>
  <tr><td>Grey</td><td><i class="box"></i></td><td><i class="box"></i></td><td><i class="box"></i></td><td><i class="box"></i></td></tr>
  <tr><td>Yellow</td><td><i class="box"></i></td><td><i class="box"></i></td><td><i class="box"></i></td><td><i class="box"></i></td></tr>
  <tr><td>Red</td><td><i class="box"></i></td><td><i class="box"></i></td><td><i class="box"></i></td><td><i class="box"></i></td></tr>
</table>

<div class="abs qty">Quantity <i></i></div>
<div class="abs rfq">ADD TO RFQ</div>
<div class="abs rule"></div>
<div class="abs shares">
  <div class="share fb"><b>Like</b><em>0</em></div>
  <div class="share"><b>Tweet</b><em>0</em></div>
  <div class="share"><b>+1</b><em>0</em></div>
  <div class="share"><b>Pin it</b></div>
</div>

<div class="abs tab active" style="left:119px;width:103px">Overview</div>
<div class="abs tab" style="left:233px;width:86px">Specs</div>
<div class="abs tab" style="left:328px;width:145px">Extended Specs</div>
<div class="abs tab-body"></div>
<p class="abs overview">It is a long established fact that a reader will be distracted by the readable content of a page when looking at its layout. The point of using Lorem Ipsum is that it has a more-or-less normal distribution of letters, as opposed to using 'Content here, content here', making it look like readable English. Many desktop publishing packages and web page editors now use Lorem Ipsum as their default model text, and a search for 'lorem ipsum' will uncover many web sites still in their infancy. Various versions have evolved over the years, sometimes by accident, sometimes on purpose (injected humour and the like).</p>
<div class="abs email">
  <svg width="14" height="10" viewBox="0 0 14 10"><rect width="14" height="10" fill="var(--red)"/><path d="M0 0l7 5 7-5" fill="none" stroke="#fff" stroke-width="1.2"/></svg>
  <a href="#">Email this product to a friend</a>
</div>

<footer class="abs footer"></footer>
<div class="abs f-head" style="left:98px">Navigation</div>
<ul class="abs f-links" style="left:98px"><li>Rescue Gear</li><li>Footwear</li><li>Clothing</li><li>Tents Mats</li><li>Sleeping Bags</li><li>Camping Gear</li><li>Snow Sports</li><li>Brands</li></ul>
<div class="abs f-head" style="left:266px">Products</div>
<ul class="abs f-links" style="left:266px"><li>Rescue Gear</li><li>Footwear</li><li>Clothing</li><li>Tents Mats</li><li>Sleeping Bags</li><li>Camping Gear</li><li>Snow Sports</li><li>Brands</li></ul>
<div class="abs f-head" style="left:422px">Get informed for our Special offers</div>
<p class="abs f-note">Get the best and most interesting discount offers via email.</p>
<div class="abs f-input"><span>you@example.com</span><b>Enter</b></div>
<div class="abs f-head" style="left:735px">Quick Contact</div>
<div class="abs field" style="top:976px;height:20px">Name:</div>
<div class="abs field" style="top:1003px;height:20px">Email:</div>
<div class="abs field" style="top:1030px;height:20px">Phone:</div>
<div class="abs field" style="top:1058px;height:57px">Message:</div>
<div class="abs submit">SUMBIT</div>
<div class="abs copy">CopyRight © 2014 NORTHKIT All Received</div>

</body>
</html>
```